Counseling Practice Business Card

I need a professional looking business card incorporating my new logo that was just completed. Card needs to incorporate my name and title, description of my specialty, my address, my phone number, my fax number, my email and my website URL. I need to be able to choose design on/with different paper colors and textures.
I do not have a lot of business card ideas so I am open to anything but I want bold,sharp, clear card without additional designs other than my logo (see attached file info). I am open to different color backgrounds or paper colors including black. I do not like traditional brackets around area codes in phone number or dashes between numbers in phone number. Am open to other ways of presenting including periods between numbers as appropriate. I do not know enough to know what I like yet but I want card to coordinate and work together with my logo. My practice emphasizes natural mental health interventions so any use of color (with background paper color or the blue and green in my logo) that elicits nature is nice. In addition to black, any natural brown or wood looking background might be desirable also. Most of the offerings so far look very similar and boring.

Target Market(s)

Potential therapy clients and other professionals

Contact Information for Business Card

Card information:
Gerald M. Whitcombe, Ph.D.
Licensed Clinical Psychologist
Integrative Health Coach
4812 Marlowe Ridge Blvd SE
Suite 310
Duluth, GA 30096
(770) 415-2983 phone
(770) 581-4096 fax
drgeraldwhitcombe@quillmarsh.net
brightfernwellness.net

Font styles to use
Serif
Sans Serif
Other font styles liked:
• anything that you think looks crisp, clear and easily readable

Requirements
Must have
• Any color used should coordinate with my logo design (see attached files).
• Card should be printed horizontally so top and bottom are longest sides of rectangle.
• Background color or paper color should complement and highlight logo. Do not like a white background. black, grey, brown or any color my logo would blend well with.
Nice to have
• I would like designer to utilize color to highlight letters/name or phone-fax-web symbols.
• Bottom edge of card could be highlighted if appropriate to an idea.
Should not have
• I would NOT want the card to have a pure white background at all.
• No clear cards.
• Cards should be oriented with long sides on bottom and top, NOT sides. DO NOT LIKE THIS THIN TALL ORIENTATION.

```html
<!DOCTYPE html>
<html lang="en">
<head>
<meta charset="utf-8">
<title>Brightfern Wellness – Business Card</title>
<link rel="stylesheet" href="https://fonts.googleapis.com/css2?family=Lato:ital,wght@0,400;0,700;0,900;1,400&display=swap">
<style>
  :root {
    --page-bg: #e6e4df;
    --card-top: #e4e8e9;
    --card-top-edge: #cfd5d7;
    --green-light: #2f6c48;
    --green-dark: #17442b;
    --brand-blue: #1d4f9c;
    --brand-green: #1a4a2e;
    --contact-text: #e3e6e2;
    --name-text: #b5b29c;
    --title-text: #e9ebe6;
  }
  * { margin: 0; padding: 0; box-sizing: border-box; }
  html, body {
    width: 1200px; height: 970px; overflow: hidden;
    background: var(--page-bg);
    font-family: "Lato", Arial, sans-serif;
  }
  .card {
    position: absolute; left: 100px; top: 186px;
    width: 1000px; height: 597px;
    overflow: hidden;
    box-shadow: 0 10px 30px rgba(0,0,0,.18);
  }
  .card-art { position: absolute; inset: 0; }
  .brand {
    position: absolute; left: 0; width: 100%; top: 118px;
    display: flex; justify-content: center; align-items: center; gap: 16px;
  }
  .brand-dot {
    width: 22px; height: 22px; border-radius: 50%;
    background: var(--brand-blue);
  }
  .brand-name {
    font-weight: 900; font-size: 54px; letter-spacing: .5px;
    color: var(--brand-green);
  }
  .contact { position: absolute; left: 67px; top: 424px; color: var(--contact-text); }
  .contact-line {
    display: flex; align-items: center; gap: 12px;
    font-size: 19px; height: 33.5px;
  }
  .contact-line svg { width: 18px; height: 18px; fill: var(--contact-text); }
  .contact-address { font-weight: 700; font-size: 18.5px; margin-top: 4px; }
  .person {
    position: absolute; right: 47px; top: 437px; text-align: right;
  }
  .person-name { font-weight: 700; font-size: 22px; color: var(--name-text); }
  .person-name .degree { font-weight: 400; font-style: italic; margin-left: 10px; }
  .person-title {
    font-style: italic; font-size: 18px; color: var(--title-text);
    line-height: 29px;
  }
  .person-title:first-of-type { margin-top: 12px; }
</style>
</head>
<body>
  <div class="card">
    <svg class="card-art" viewBox="0 0 1000 597" width="1000" height="597" aria-hidden="true">
      <defs>
        <linearGradient id="topFill" x1="0" y1="0" x2="0" y2="1">
          <stop offset="0" stop-color="var(--card-top)"/>
          <stop offset="1" stop-color="var(--card-top-edge)"/>
        </linearGradient>
        <linearGradient id="greenFill" x1="0" y1="0" x2="0" y2="1">
          <stop offset="0" stop-color="var(--green-light)"/>
          <stop offset="1" stop-color="var(--green-dark)"/>
        </linearGradient>
      </defs>
      <rect width="1000" height="597" fill="url(#topFill)"/>
      <path d="M0 379 Q500 222 1000 379 L1000 597 L0 597 Z" fill="url(#greenFill)"/>
      <path d="M39 353 Q500 198 960 353 Q500 216 39 353 Z" fill="var(--brand-blue)"/>
    </svg>

    <div class="brand">
      <span class="brand-dot"></span>
      <span class="brand-name">Brightfern Wellness</span>
    </div>

    <div class="contact">
      <div class="contact-line">
        <svg viewBox="0 0 24 24"><path d="M6.6 10.8a15.1 15.1 0 0 0 6.6 6.6l2.2-2.2a1 1 0 0 1 1-.25 11.4 11.4 0 0 0 3.6.57 1 1 0 0 1 1 1V20a1 1 0 0 1-1 1A17 17 0 0 1 3 4a1 1 0 0 1 1-1h3.5a1 1 0 0 1 1 1c0 1.25.2 2.45.57 3.57a1 1 0 0 1-.25 1z"/></svg>
        <span>770 415-2983</span>
      </div>
      <div class="contact-line">
        <svg viewBox="0 0 24 24"><path d="M6 2h10v5H6zM3 8h18a1 1 0 0 1 1 1v8h-4v5H6v-5H2V9a1 1 0 0 1 1-1zm5 8v4h8v-4z"/></svg>
        <span>770 581-4096</span>
      </div>
      <div class="contact-line">
        <svg viewBox="0 0 24 24"><path d="M2 5h20v14H2zm2 2v.4l8 5.2 8-5.2V7zm0 2.8V17h16V9.8l-8 5.2z"/></svg>
        <span>drgeraldwhitcombe@quillmarsh.net</span>
      </div>
      <div class="contact-address">4812 Marlowe Ridge Blvd SE, Suite 310, Duluth, GA 30096</div>
    </div>

    <div class="person">
      <div class="person-name">Gerald M. Whitcombe<span class="degree">Ph.D</span></div>
      <div class="person-title">Licensed Clinical Psychologist</div>
      <div class="person-title">Integrative Health Coach</div>
    </div>
  </div>
</body>
</html>
```